Compnay PowerPoint Tempalte Design

I am needing a good base design and slide designs for interior and exterior company presentations. The template will need to be on the company brand with proper coloring and fonts. Able to be creative with layout options with a good example attached.
website for reference: www.crewvlt.com/

Target Market(s)

Professionals

Font styles to use
Other font styles liked:
• Helvetica

Requirements
Must have
• On Brand Colors, Clean, simple design

```html
<!DOCTYPE html>
<html lang="en">
<head>
<meta charset="utf-8">
<title>VLT Presentation Template</title>
<link rel="stylesheet" href="https://fonts.googleapis.com/css2?family=Open+Sans:wght@400;700;800&family=Arimo:wght@400;700&display=swap">
<style>
  :root {
    --canvas: #85878b;
    --paper: #ffffff;
    --ink: #1b1b1b;
    --brand-blue: #1d6a94;
    --brand-teal: #3a8a7e;
    --brand-green: #2a7a62;
    --brand-green-light: #5fa897;
    --panel-tint: #f4f1f1;
  }
  * { margin: 0; padding: 0; box-sizing: border-box; }
  html, body { width: 1200px; height: 3288px; overflow: hidden; background: var(--canvas); }
  body { position: relative; font-family: "Arimo", Helvetica, Arial, sans-serif; color: var(--ink); }

  .slide { position: absolute; left: 115px; width: 1002px; height: 563px; background: var(--paper); overflow: hidden; }
  .slide--welcome { top: 92px; }
  .slide--services { top: 725px; }
  .slide--about { top: 1357px; }
  .slide--values { top: 1989px; }
  .slide--culture { top: 2621px; }

  .wordmark { position: absolute; font-family: "Open Sans", Arial, sans-serif; font-weight: 800; color: var(--ink); letter-spacing: 1px; line-height: 1; }
  .wordmark--corner { left: 15px; bottom: 14px; font-size: 52px; }

  .slide-title { position: absolute; font-family: "Open Sans", Arial, sans-serif; font-weight: 700; font-size: 31px; letter-spacing: 1px; color: var(--ink); line-height: 1; }

  .bar { position: absolute; }
  .bar--blue { background: var(--brand-blue); }
  .bar--teal { background: var(--brand-teal); }

  .photo { position: absolute; }

  /* Welcome */
  .welcome-hero { position: absolute; inset: 0; }
  .welcome-mark { left: 0; width: 424px; top: 200px; text-align: center; font-size: 62px; }
  .welcome-title { left: 0; width: 424px; top: 298px; text-align: center; }
  .welcome-lede { position: absolute; left: 0; width: 424px; top: 354px; text-align: center; font-family: "Open Sans", Arial, sans-serif; font-size: 19px; line-height: 25px; }

  /* Services */
  .service-tile { position: absolute; top: 27px; height: 352px; width: 307px; display: flex; align-items: center; justify-content: center; }
  .service-tile span { font-family: "Arimo", Helvetica, Arial, sans-serif; font-weight: 700; font-size: 31px; color: #fff; letter-spacing: 1px; }
  .tile-restaurants { left: 22px; background: linear-gradient(160deg, #1f3a3e, #3a2a1e 70%, #14181a); }
  .tile-realestate { left: 346px; background: linear-gradient(170deg, #3f86d8, #23508a 55%, #1c2a44); }
  .tile-development { left: 673px; background: linear-gradient(170deg, #6a4a36, #c9c4bd 45%, #e6e6e8); }
  .title-rule { position: absolute; left: 150px; top: 497px; width: 195px; height: 3px; background: var(--brand-teal); }

  /* About */
  .team-photo { left: 6px; top: 5px; width: 992px; height: 388px; background: linear-gradient(100deg, #cfc9bf, #5a6f80 25%, #2e2b2b 50%, #8a8784 75%, #d9d6d2); }
  .about-panel { position: absolute; left: 359px; top: 323px; width: 620px; height: 222px; background: var(--panel-tint); padding: 34px 40px 0 46px; font-size: 15.5px; line-height: 22px; }

  /* Values */
  .value-card { position: absolute; width: 449px; height: 150px; border: 2px solid var(--brand-blue); }
  .value-card .marker { position: absolute; left: 24px; top: 42px; width: 34px; height: 34px; background: var(--brand-teal); }
  .value-card h3 { position: absolute; left: 110px; top: 32px; font-family: "Arimo", Helvetica, Arial, sans-serif; font-size: 23px; font-weight: 700; color: var(--brand-blue); }
  .value-card p { position: absolute; left: 111px; top: 68px; right: 20px; font-size: 17px; line-height: 23px; }

  /* Culture */
  .culture-photo { left: 475px; top: 0; width: 527px; height: 563px; background: linear-gradient(160deg, #e8ecee, #c7d1d6 45%, #3a4246 70%, #e9ecee); }
  .culture-headline { position: absolute; left: 40px; width: 395px; top: 108px; text-align: center; font-family: "Arimo", Helvetica, Arial, sans-serif; font-weight: 700; font-size: 28px; line-height: 34px; color: var(--brand-blue); }
  .culture-body { position: absolute; left: 60px; width: 355px; top: 237px; text-align: center; font-size: 17.5px; line-height: 26px; }
</style>
</head>
<body>

<section class="slide slide--welcome">
  <svg class="welcome-hero" width="1002" height="563" viewBox="0 0 1002 563">
    <defs>
      <linearGradient id="heroTone" x1="0" y1="0" x2="1" y2="1">
        <stop offset="0" stop-color="#1f6a55"/>
        <stop offset="0.6" stop-color="#2f7f66"/>
        <stop offset="1" stop-color="#5fa897"/>
      </linearGradient>
    </defs>
    <polygon points="470,0 1002,0 1002,563 415,563" fill="url(#heroTone)" role="img" aria-label="Photo of colleagues smiling over coffee, tinted green"/>
  </svg>
  <div class="wordmark welcome-mark">VLT</div>
  <h1 class="slide-title welcome-title">WELCOME TO VLT</h1>
  <p class="welcome-lede">Lorem Ipsum is simply dummy<br>text of the printing and type<br>sett ing industry</p>
  <div class="bar bar--blue" style="left:0;top:527px;width:209px;height:10px"></div>
  <div class="bar bar--teal" style="left:0;top:537px;width:259px;height:26px"></div>
</section>

<section class="slide slide--services">
  <div class="service-tile tile-restaurants" role="img" aria-label="Photo of a dimly lit restaurant bar"><span>RESTAURANTS</span></div>
  <div class="service-tile tile-realestate" role="img" aria-label="Photo of glass skyscrapers from below"><span>REAL ESTATE</span></div>
  <div class="service-tile tile-development" role="img" aria-label="Photo of a team meeting around laptops"><span>DEVELOPMENT</span></div>
  <div class="wordmark wordmark--corner">VLT</div>
  <div class="title-rule"></div>
  <h2 class="slide-title" style="left:150px;top:516px">WHAT WE DO</h2>
  <div class="bar bar--blue" style="left:521px;top:526px;width:476px;height:12px"></div>
  <div class="bar bar--teal" style="left:537px;top:536px;width:465px;height:27px"></div>
</section>

<section class="slide slide--about">
  <div class="photo team-photo" role="img" aria-label="Photo of five smiling team members standing together"></div>
  <div class="about-panel">VLT is dedicated to cultivating a positive culture of leadership for its team members’ professional and personal development, and this person-focused mentality transfers throughout the company from partners to our teams to guests. We strive to ensure each team member feels valued in all aspects of their role, reinforcing the importance of fostering a self-sustaining culture of success where everyone makes a team effort to communicate and overcome adversity.</div>
  <div class="wordmark wordmark--corner">VLT</div>
  <h2 class="slide-title" style="left:155px;top:517px">ABOUT US</h2>
</section>

<section class="slide slide--values">
  <div class="value-card" style="left:41px;top:47px"><span class="marker"></span><h3>INTEGRITY</h3><p>Integrity in everything we do. Do the right thing, even when no one is looking.</p></div>
  <div class="value-card" style="left:512px;top:47px"><span class="marker"></span><h3>FAMILY</h3><p>Family first, always. All decisions must benefit our family and the company.</p></div>
  <div class="value-card" style="left:41px;top:231px"><span class="marker"></span><h3>RESPECT</h3><p>We care for one another, praise efforts, recognize progress, and reward results.</p></div>
  <div class="value-card" style="left:512px;top:231px"><span class="marker"></span><h3>PASSION</h3><p>We are positive, hardworking, and disciplined in all we do, which stems from our innate passion.</p></div>
  <div class="wordmark wordmark--corner">VLT</div>
  <h2 class="slide-title" style="left:148px;top:513px">OUR CORE VALUES</h2>
  <div class="bar bar--blue" style="left:519px;top:526px;width:475px;height:12px"></div>
  <div class="bar bar--teal" style="left:536px;top:536px;width:466px;height:27px"></div>
</section>

<section class="slide slide--culture">
  <h2 class="culture-headline">LOREM IPSUM IS SIMPLY DUMMY TEXT OF THE PRINTING</h2>
  <p class="culture-body">Our culture is founded on four core values and the entrepreneurial spirit of ownership that comes from a foundation of passion for our people, commitment to our business, transparency, and continued progress.</p>
  <div class="wordmark wordmark--corner">VLT</div>
  <div class="photo culture-photo" role="img" aria-label="Photo of two women reviewing a tablet at an office desk"></div>
</section>

</body>
</html>
```